Real Estate Brokerage Stationery Designs

I am looking to have presentation folders with business card slots on both sides along with pockets on both sides. I've attached logos, website colors along with current business card designs.

I am looking for envelope designs both big and small. Possibly new business card designs, notepad templates for big and small notepads. Letterhead designs. Pop socket designs. Realtors name badge designs.

www.brightholdrealty.example

```html
<!DOCTYPE html>
<html lang="en">
<head>
<meta charset="utf-8">
<title>Brighthold Realty – Presentation Folder</title>
<link rel="stylesheet" href="https://fonts.googleapis.com/css2?family=Open+Sans:wght@400;600;700&family=Oswald:wght@500&display=swap">
<style>
  :root {
    --navy: #0d4fa3;
    --blue: #3f88d8;
    --sky: #6aa7e8;
    --pale: #a9cff5;
    --ink: #141a2a;
    --paper: #ffffff;
    --grey: #dcdcdc;
    --strip: #111111;
  }
  html, body { margin: 0; padding: 0; overflow: hidden; }
  body {
    width: 1200px; height: 1080px;
    background: linear-gradient(180deg, #cfe4fb 0%, #8fbff2 100%);
    font-family: "Open Sans", sans-serif;
  }
  .spread { position: absolute; left: 240px; width: 720px; height: 480px; box-shadow: 0 10px 30px rgba(20,60,120,.25); }
  .spread--outside { top: 40px; }
  .spread--inside { top: 560px; }
  .spread svg { display: block; }
  .brand-name { font-family: "Open Sans", sans-serif; font-weight: 700; fill: var(--ink); }
  .url { font-family: "Open Sans", sans-serif; font-weight: 700; fill: #fff; font-size: 13px; }
  .contact { font-family: "Open Sans", sans-serif; font-weight: 600; fill: var(--navy); font-size: 7.5px; }
  .services { font-family: "Open Sans", sans-serif; font-weight: 600; fill: #8a8f99; font-size: 8px; }
  .pill-label { font-family: "Open Sans", sans-serif; font-weight: 700; fill: #fff; font-size: 8px; letter-spacing: .5px; }
  .card-name { font-family: "Oswald", sans-serif; font-weight: 500; fill: #fff; font-size: 10px; letter-spacing: .5px; }
  .card-title { font-family: "Open Sans", sans-serif; font-weight: 700; fill: #fff; font-size: 5px; letter-spacing: .5px; }
  .card-brand { font-family: "Open Sans", sans-serif; font-weight: 700; fill: var(--navy); font-size: 9px; }
  .card-small { font-family: "Open Sans", sans-serif; fill: #333; font-size: 4.6px; }
</style>
</head>
<body>

<!-- Outside of folder: back cover + front cover -->
<div class="spread spread--outside">
  <svg width="720" height="480" viewBox="0 0 720 480">
    <defs>
      <linearGradient id="roomBlue" x1="0" y1="0" x2="1" y2="1">
        <stop offset="0" stop-color="#2a6cc4"/><stop offset=".6" stop-color="#6b8fb8"/><stop offset="1" stop-color="#d9cfc4"/>
      </linearGradient>
      <linearGradient id="roomPale" x1="0" y1="0" x2="1" y2="1">
        <stop offset="0" stop-color="#a9c9ec"/><stop offset=".6" stop-color="#c7d6e6"/><stop offset="1" stop-color="#7a4c8e"/>
      </linearGradient>
    </defs>

    <!-- Back cover -->
    <g class="back-cover">
      <rect x="0" y="0" width="360" height="480" fill="var(--paper)"/>
      <polygon points="0,0 360,0 360,40 0,110" fill="var(--navy)"/>
      <polygon points="0,110 360,40 360,300 0,250" fill="url(#roomBlue)" role="img" aria-label="Photo of a child's bedroom with bunk bed and aquarium"/>
      <polygon points="0,250 360,300 360,330 0,275" fill="var(--sky)"/>
      <polygon points="0,275 360,330 360,345 0,300" fill="var(--blue)"/>
      <polygon points="0,300 360,345 360,380 0,380" fill="var(--pale)" opacity=".55"/>

      <!-- contact row -->
      <g class="contact-row">
        <circle cx="80" cy="362" r="10" fill="var(--ink)"/>
        <circle cx="78" cy="360" r="3.5" fill="none" stroke="#fff" stroke-width="1.4"/>
        <line x1="80.5" y1="362.5" x2="84" y2="366" stroke="#fff" stroke-width="1.6"/>
        <text class="contact" x="80" y="384" text-anchor="middle">hello@brightholdrealty.example</text>
        <text class="contact" x="80" y="394" text-anchor="middle">www.brightholdrealty.example</text>

        <circle cx="185" cy="356" r="10" fill="var(--ink)"/>
        <circle cx="185" cy="353" r="2.8" fill="#fff"/>
        <path d="M179.5 361 q5.5 -6 11 0 z" fill="#fff"/>
        <text class="contact" x="185" y="378" text-anchor="middle">555-010-2715</text>
        <text class="contact" x="185" y="388" text-anchor="middle">555-010-0455</text>

        <circle cx="285" cy="348" r="10" fill="var(--ink)"/>
        <path d="M279 349 l6 -6 l6 6 h-2 v5 h-8 v-5 z" fill="#fff"/>
        <text class="contact" x="285" y="370" text-anchor="middle">1200 Harbor Way, Ste 210,</text>
        <text class="contact" x="285" y="380" text-anchor="middle">Lakeview, FL 00000</text>
      </g>

      <rect x="130" y="400" width="100" height="14" rx="7" fill="var(--navy)"/>
      <text class="pill-label" x="180" y="410" text-anchor="middle">SERVICES</text>
      <line x1="0" y1="420" x2="360" y2="420" stroke="var(--sky)" stroke-width="2"/>
      <text class="services" x="14" y="442" textLength="332" lengthAdjust="spacingAndGlyphs">Residential Real Estate | Commercial Real Estate | Property Management | Investments</text>
      <rect x="0" y="460" width="360" height="20" fill="var(--strip)"/>
    </g>

    <!-- Front cover -->
    <g class="front-cover">
      <rect x="360" y="0" width="360" height="480" fill="url(#roomPale)" role="img" aria-label="Photo of a girl's bedroom with white bed and plush toys"/>
      <polygon points="360,0 720,0 720,10 360,230" fill="var(--navy)"/>
      <polygon points="720,10 720,0 360,230 360,245" fill="var(--sky)" opacity=".8"/>
      <path d="M380 38 l9 5 l-9 5 z" fill="#fff"/>
      <text class="url" x="396" y="48">www.brightholdrealty.example</text>
      <polygon points="360,360 720,170 720,460 360,460" fill="var(--blue)"/>
      <polygon points="360,360 720,170 720,190 360,378" fill="var(--navy)"/>
      <polygon points="360,395 720,240 720,460 360,460" fill="var(--sky)" opacity=".6"/>
      <rect x="470" y="387" width="12" height="12" fill="var(--navy)"/>
      <text class="brand-name" x="490" y="400" font-size="20">Brighthold Realty</text>
      <rect x="360" y="460" width="360" height="20" fill="var(--strip)"/>
    </g>
    <line x1="360" y1="0" x2="360" y2="480" stroke="rgba(0,0,0,.15)"/>
  </svg>
</div>

<!-- Inside of folder: two pockets with business card slots -->
<div class="spread spread--inside">
  <svg width="720" height="480" viewBox="0 0 720 480">
    <defs>
      <linearGradient id="portrait" x1="0" y1="0" x2="0" y2="1">
        <stop offset="0" stop-color="#e8e8e8"/><stop offset="1" stop-color="#9a8478"/>
      </linearGradient>
    </defs>
    <rect x="0" y="0" width="360" height="480" fill="var(--paper)"/>
    <rect x="360" y="0" width="360" height="480" fill="var(--grey)"/>
    <line x1="360" y1="0" x2="360" y2="480" stroke="rgba(0,0,0,.12)"/>

    <!-- left pocket -->
    <g class="pocket pocket--left">
      <path d="M0 320 H352 V480 H0 Z" fill="var(--sky)"/>
      <line x1="0" y1="320" x2="352" y2="320" stroke="var(--blue)" stroke-width="2"/>
      <g class="business-card" transform="translate(70 345)">
        <path d="M12 0 H210 V110 H0 V12 Z" fill="#fff"/>
        <rect x="12" y="18" width="7" height="7" fill="var(--navy)"/>
        <text class="card-brand" x="23" y="25">Brighthold Realty</text>
        <text class="card-small" x="12" y="60">Residential Real Estate | Commercial Real Estate</text>
        <text class="card-small" x="12" y="67">Property Management | Investments</text>
        <rect x="12" y="80" width="12" height="12" fill="#222"/>
        <rect x="28" y="80" width="12" height="12" fill="#222"/>
        <rect x="130" y="0" width="80" height="110" fill="url(#portrait)" role="img" aria-label="Portrait photo of the broker"/>
        <path d="M110 88 H210 V104 L204 110 H104 Z" fill="var(--ink)"/>
        <text class="card-name" x="200" y="100" text-anchor="end">MARCUS ELLERY</text>
        <text class="card-title" x="200" y="107" text-anchor="end">BROKER</text>
      </g>
    </g>

    <!-- right pocket -->
    <g class="pocket pocket--right">
      <path d="M368 320 H720 V480 H368 Z" fill="var(--blue)"/>
      <line x1="368" y1="320" x2="720" y2="320" stroke="var(--navy)" stroke-width="2"/>
      <g class="business-card" transform="translate(440 345)">
        <path d="M12 0 H210 V98 L198 110 H0 V12 Z" fill="#fff"/>
        <rect x="12" y="18" width="7" height="7" fill="var(--navy)"/>
        <text class="card-brand" x="23" y="25">Brighthold Realty</text>
        <text class="card-small" x="12" y="60">Residential Real Estate | Commercial Real Estate</text>
        <text class="card-small" x="12" y="67">Property Management | Investments</text>
        <rect x="12" y="80" width="12" height="12" fill="#222"/>
        <rect x="28" y="80" width="12" height="12" fill="#222"/>
        <rect x="130" y="0" width="80" height="110" fill="url(#portrait)" role="img" aria-label="Portrait photo of the realtor"/>
        <path d="M110 84 H210 V98 L198 110 H104 Z" fill="var(--ink)"/>
        <text class="card-name" x="200" y="96" text-anchor="end">DANIEL VANCE</text>
        <text class="card-title" x="196" y="105" text-anchor="end">REALTOR</text>
      </g>
    </g>
  </svg>
</div>

</body>
</html>
```